Canadian Christian Church needs design for new sermon series

A graphic design for our series and an invitation card to invite people to the series. Check design brief for more detailed information. Target audience: young families and young adults. Looking for a creative design that will get people's attention and create interest. See design brief for copy of design purchased for previous series.
Updates
entered Apr 4 incorrectly. Need a week to receive and review designs, and today is Apr 2/19. Thanks!
Target Market(s)
young families and young adults
Colors
Designer to choose colors to be used in the design.
Look and feel

```html
<!DOCTYPE html>
<html lang="en">
<head>
<meta charset="utf-8">
<title>Messy – Sermon Series Invitation</title>
<link rel="stylesheet" href="https://fonts.googleapis.com/css2?family=Montserrat:wght@500;600;700;800&family=Crimson+Pro:wght@600;700&family=Lato:wght@400&display=swap">
<style>
  :root {
    --backdrop: #e2e2e2;
    --cocoa: #3b302d;
    --night: #15141a;
    --white: #ffffff;
    --rule: #4a3c37;
    --rule-light: #f3efe6;
  }
  * { margin: 0; padding: 0; box-sizing: border-box; }
  html, body { width: 1200px; height: 1200px; overflow: hidden; background: var(--backdrop); }
  body { position: relative; font-family: "Montserrat", sans-serif; }

  .card { position: absolute; left: 296px; width: 609px; height: 480px; overflow: hidden; }

  /* Front */
  .card--front { top: 120px; background: linear-gradient(100deg, #e1d9ca 0%, #d3cab8 45%, #b3a792 100%); }
  .front__photo {
    position: absolute; right: 0; top: 0; width: 330px; height: 100%;
    background:
      radial-gradient(ellipse 55% 60% at 68% 45%, #4a4038 0%, #3a322c 45%, rgba(90,80,68,0) 100%),
      linear-gradient(90deg, rgba(160,148,128,0) 0%, rgba(120,108,92,0.7) 45%, #6e6252 100%);
  }
  .front__fade {
    position: absolute; left: 0; right: 0; bottom: 0; height: 160px;
    background: linear-gradient(180deg, rgba(21,20,26,0) 0%, rgba(21,20,26,0.8) 50%, var(--night) 100%);
  }
  .front__curves, .back__curves { position: absolute; inset: 0; }
  .front__frame {
    position: absolute; left: 10px; top: 13px; right: 8px; bottom: 12px;
    border: 1.5px solid #3a2f2b;
  }
  .brand {
    position: absolute; left: 32px; top: 46px;
    display: flex; flex-direction: column; align-items: center; gap: 10px; width: 180px;
  }
  .brand__dot { width: 62px; height: 62px; border-radius: 50%; background: var(--cocoa); }
  .brand__name { font-weight: 500; font-size: 13px; color: var(--cocoa); white-space: nowrap; }
  .series-title {
    position: absolute; left: 34px; top: 193px;
    font-weight: 800; font-size: 102px; line-height: 1; letter-spacing: 2px; color: var(--cocoa);
  }
  .series-tagline {
    position: absolute; left: 33px; top: 288px;
    width: 443px; height: 45px; background: var(--cocoa);
    display: flex; align-items: center; padding-left: 18px;
    font-family: "Crimson Pro", serif; font-weight: 700; font-size: 33px; color: var(--white);
    letter-spacing: 0.3px; white-space: nowrap;
  }
  .front__web {
    position: absolute; left: 32px; top: 416px;
    font-family: "Crimson Pro", serif; font-weight: 600; font-size: 18px; letter-spacing: 2.2px; color: var(--white);
  }

  /* Back */
  .card--back { top: 662px; background: linear-gradient(120deg, #d2c9b6 0%, #c4baa5 60%, #b7ac96 100%); }
  .invite { position: absolute; left: 0; right: 0; top: 26px; text-align: center; color: var(--white); font-weight: 800; }
  .invite__head { font-size: 41px; line-height: 1.05; letter-spacing: 1px; }
  .invite__time { font-size: 35px; font-weight: 700; line-height: 1.2; letter-spacing: 0.5px; }

  .topics { position: absolute; left: 24px; top: 144px; width: 364px; }
  .topics__label {
    display: inline-block; background: var(--cocoa); color: var(--white);
    font-weight: 600; font-size: 16px; letter-spacing: 0.6px; padding: 6px 7px 4px 6px;
  }
  .topics__table { width: 364px; border-collapse: collapse; color: var(--white); font-weight: 700; font-size: 16px; letter-spacing: 0.3px; }
  .topics__table td { border: 1.5px solid var(--rule); height: 25.8px; padding: 0 10px; line-height: 1; white-space: nowrap; }
  .topics__table td:first-child { width: 121px; }

  .details { position: absolute; left: 415px; top: 142px; width: 170px; color: var(--cocoa); }
  .details__head { font-weight: 700; font-size: 16px; line-height: 1.25; letter-spacing: 0.4px; }
  .details__rule { height: 1px; background: var(--rule-light); width: 144px; margin: 5px 0 10px; }
  .details__list { list-style: none; font-family: "Lato", sans-serif; font-size: 9.4px; line-height: 1.2; }
  .details__list li { position: relative; padding-left: 8px; margin-bottom: 5px; }
  .details__list li::before { content: ""; position: absolute; left: 0; top: 4px; width: 3px; height: 3px; border-radius: 50%; background: var(--cocoa); }
  .details__about { margin-top: 20px; }
  .details__text { font-family: "Lato", sans-serif; font-size: 7.6px; line-height: 1.3; width: 165px; }

  .back__footer {
    position: absolute; left: 0; right: 0; bottom: 0; height: 60px; background: var(--cocoa);
    color: var(--white); text-align: center; font-weight: 500; padding-top: 9px;
  }
  .back__footer p:first-child { font-size: 14px; line-height: 18px; }
  .back__footer p:last-child { font-size: 12.6px; line-height: 19px; }
</style>
</head>
<body>

<section class="card card--front">
  <svg class="front__curves" viewBox="0 0 609 480" aria-hidden="true">
    <path d="M60 0 C 160 80, 300 90, 460 30" fill="none" stroke="#efe9dd" stroke-opacity="0.6" stroke-width="2"/>
    <path d="M0 130 C 140 60, 300 70, 430 180" fill="none" stroke="#efe9dd" stroke-opacity="0.2" stroke-width="24"/>
    <path d="M0 260 C 80 200, 200 190, 320 240" fill="none" stroke="#efe9dd" stroke-opacity="0.15" stroke-width="14"/>
  </svg>
  <div class="front__photo" role="img" aria-label="Sepia photograph of a young boy sitting against a wall, holding a worn doll"></div>
  <div class="front__fade"></div>
  <div class="front__frame"></div>

  <div class="brand">
    <span class="brand__dot"></span>
    <span class="brand__name">Maple Grove Family Church</span>
  </div>

  <h1 class="series-title">MESSY</h1>
  <p class="series-tagline">JOINING GOD IN THE MESS</p>
  <p class="front__web">www.maplegrovechurch.ca</p>
</section>

<section class="card card--back">
  <svg class="back__curves" viewBox="0 0 609 480" aria-hidden="true">
    <path d="M10 0 C 60 90, 110 150, 250 200" fill="none" stroke="#ebe4d6" stroke-opacity="0.6" stroke-width="2"/>
    <path d="M0 170 C 150 90, 380 60, 609 120" fill="none" stroke="#ebe4d6" stroke-opacity="0.18" stroke-width="22"/>
    <path d="M320 400 C 420 330, 520 320, 609 350" fill="none" stroke="#ebe4d6" stroke-opacity="0.18" stroke-width="16"/>
  </svg>

  <div class="invite">
    <p class="invite__head">JOIN US</p>
    <p class="invite__time">Sundays @ 10:30</p>
  </div>

  <div class="topics">
    <span class="topics__label">MESSAGE TOPICS</span>
    <table class="topics__table">
      <tr><td>April 28th</td><td>We Made This Mess</td></tr>
      <tr><td>May 5th</td><td>Bless in the Mess</td></tr>
      <tr><td>May 12th</td><td>Born into the Mess</td></tr>
      <tr><td>May 19th</td><td>Messy Work</td></tr>
      <tr><td>May 26th</td><td>Messy Church</td></tr>
      <tr><td>June 2nd</td><td>Messy Hospitality</td></tr>
      <tr><td>June 9th</td><td>TBD</td></tr>
      <tr><td>June 16th</td><td>Messy within Boundaries</td></tr>
    </table>
  </div>

  <div class="details">
    <h2 class="details__head">FEATURES OF<br>THE SERVICE:</h2>
    <div class="details__rule"></div>
    <ul class="details__list">
      <li>Staffed nursery &amp; children's program every Sunday</li>
      <li>Coffee &amp; snacks</li>
      <li>Everyone welcome</li>
    </ul>
    <h2 class="details__head details__about">ABOUT THE<br>CHURCH</h2>
    <div class="details__rule"></div>
    <p class="details__text">Maple Grove Family Church is a multicultural, multi-generational Christian community, serving Brookfield and Cedar Hills. We are a part of the Fellowship of Gospel Churches in Canada.</p>
  </div>

  <footer class="back__footer">
    <p>Location - 1180 Cedar Line West Brookfield, ON&nbsp; L4R 2K8</p>
    <p>Phone-905.555.0142 | Email-info@maplegrovechurch.ca | Website-www.maplegrovechurch.ca</p>
  </footer>
</section>

</body>
</html>
```